Detail Shop Business card design

i need a business card design for my new detailing company called 'Brisk's Polish Works'. i want an all black and white design . simple, direct and to the point. i want the designer to choose a fitting font to match the logothe front should have logo, address, phone and email and the back side should have a slogan and text indicating that we offer services on anything including cars, trucks, motorcycles and RVs. slogan will read "we take pride in your ride"
maybe also very small on the back side the IG icon with Brisks_Polish_Works

phone 208.417.6352
address 3847 E Larkin Ave
Spokane WA 99214
email: BrisksPolish@mailvexo.com

Target Market(s)

all ages , auto enthusiasts

Industry/Entity Type

Automotive

Contact Information for Business Card

the front should have logo, address, phone and email and the back side should have a slogan and text indicating that we offer services on anything including cars, trucks, motorcycles and RVs. slogan will read "we take pride in your ride"

phone 208.417.6352
address 3847 E Larkin Ave
Spokane WA 99214

Colors
000000
ffffff

Requirements
Must have
• bold font and very simple design with good spacing
Nice to have
• anything creative from the designer indicating we service any types of vehicles
Should not have
• any colors ,

```html
<!DOCTYPE html>
<html lang="en">
<head>
<meta charset="utf-8">
<title>Brisk's Polish Works – Business Card</title>
<link rel="stylesheet" href="https://fonts.googleapis.com/css2?family=Lato:wght@400;900&display=swap">
<style>
  :root {
    --backdrop: #e4e4e4;
    --paper: #ffffff;
    --ink: #000000;
  }
  * { margin: 0; padding: 0; box-sizing: border-box; }
  html, body { width: 1200px; height: 900px; overflow: hidden; }
  body {
    background: var(--backdrop);
    font-family: "Lato", sans-serif;
    color: var(--ink);
    position: relative;
  }
  .card {
    position: absolute;
    width: 556px;
    height: 343px;
    background: var(--paper);
  }
  .card--front { left: 330px; top: 90px; }
  .card--back  { left: 331px; top: 469px; }

  .brand {
    position: absolute;
    left: 0; right: 0;
    top: 120px;
    display: flex;
    align-items: center;
    justify-content: center;
    gap: 14px;
  }
  .brand__dot {
    width: 22px; height: 22px;
    border-radius: 50%;
    background: var(--ink);
  }
  .brand__name {
    font-weight: 900;
    font-size: 34px;
    letter-spacing: 0.5px;
    text-transform: uppercase;
  }
  .slogan {
    position: absolute;
    left: 0; right: 0;
    top: 277px;
    text-align: center;
    font-size: 20px;
    letter-spacing: 0.3px;
  }

  .contact {
    position: absolute;
    left: 0; right: 0;
    top: 61px;
    text-align: center;
    font-size: 16px;
    line-height: 20px;
  }
  .rule {
    width: 180px;
    height: 1px;
    background: var(--ink);
    margin: 11px auto 14px;
  }
  .rule--marked {
    position: relative;
    margin: 18px auto 14px;
  }
  .rule--marked::after {
    content: "";
    position: absolute;
    left: 50%; top: 50%;
    width: 22px; height: 22px;
    margin: -11px 0 0 -11px;
    border-radius: 50%;
    background: var(--ink);
  }
  .rule--closing { margin: 15px auto 0; }
  .services {
    margin-top: 12px;
    line-height: 25px;
  }
</style>
</head>
<body>
  <section class="card card--front">
    <div class="brand">
      <span class="brand__dot"></span>
      <span class="brand__name">Brisk's Polish Works</span>
    </div>
    <p class="slogan">WE TAKE PRIDE IN YOUR RIDE</p>
  </section>

  <section class="card card--back">
    <div class="contact">
      <p>208.417.6352</p>
      <p>BrisksPolish@mailvexo.com</p>
      <div class="rule"></div>
      <p>3847 E Larkin Ave</p>
      <p>Spokane WA 99214</p>
      <div class="rule rule--marked"></div>
      <p>Brisks_Polish_Works</p>
      <div class="rule rule--closing"></div>
      <p class="services">We offer services on anything including<br>cars, trucks, motorcycles and RVs.</p>
    </div>
  </section>
</body>
</html>
```